Business Card Design for company

We want new business cards. We'd like something different-- yet still highly professional. Our tagline is Guiding strategy, building results. Stock photos are ok, as long as they are relevant and look upscale.

Target Market(s)

Architecture/Business Management Consulting/Engineering Consulting

Contact Information for Business Card

dark gray background with pops of blue might be good, but you tell me. You're the designers. Rounded corners might be nice, but again, you tell me.

Font styles to use
Serif
Sans Serif

Colors
3276b5
5c5c5c
9d9d9d
fbfbfb

Requirements
Nice to have
• Something different, but still very professional.

```html
<!DOCTYPE html>
<html lang="en">
<head>
<meta charset="utf-8">
<title>Veltra Partners — Business Card</title>
<link rel="stylesheet" href="https://fonts.googleapis.com/css2?family=Roboto:wght@400;500;700&display=swap">
<style>
  :root {
    --blue: #23609a;
    --slate: #4a4d52;
    --ink: #4b4e53;
    --paper: #ffffff;
    --stage: #e6e6e6;
    --line: #3276b5;
  }
  html, body {
    margin: 0;
    padding: 0;
    width: 1200px;
    height: 1108px;
    overflow: hidden;
    background: var(--stage);
    font-family: "Roboto", sans-serif;
  }
  .canvas {
    position: relative;
    width: 1200px;
    height: 1108px;
  }
  .card {
    position: absolute;
    left: 220px;
    width: 760px;
    height: 434px;
    box-shadow: 0 10px 28px rgba(0,0,0,0.18);
    overflow: hidden;
  }
  .card-back {
    top: 86px;
    background: var(--slate);
  }
  .card-front {
    top: 588px;
    background: var(--paper);
  }

  /* Back */
  .back-wordmark {
    position: absolute;
    left: 0;
    right: 0;
    top: 150px;
    text-align: center;
    color: var(--blue);
    font-weight: 700;
    font-size: 64px;
    letter-spacing: 2px;
  }
  .back-tagline {
    position: absolute;
    left: 0;
    right: 0;
    top: 262px;
    margin: 0;
    text-align: center;
    color: #ffffff;
    font-size: 18px;
    font-weight: 400;
    letter-spacing: 0.5px;
  }
  .back-tagline .dot {
    display: inline-block;
    width: 6px;
    height: 6px;
    border-radius: 50%;
    background: #ffffff;
    margin: 0 10px 3px;
  }

  /* Front */
  .front-wordmark {
    position: absolute;
    left: 44px;
    top: 92px;
    width: 300px;
    color: var(--blue);
    font-weight: 700;
    font-size: 56px;
    line-height: 1.02;
    letter-spacing: 1px;
  }
  .details {
    position: absolute;
    left: 400px;
    top: 70px;
    width: 320px;
    color: var(--ink);
  }
  .row {
    position: relative;
    padding-left: 36px;
  }
  .row svg {
    position: absolute;
    left: 0;
    width: 18px;
    height: 18px;
    fill: var(--blue);
  }
  .person-name {
    color: var(--blue);
    font-weight: 700;
    font-size: 25px;
    letter-spacing: 0.5px;
    line-height: 1.1;
  }
  .person-title {
    font-weight: 700;
    font-size: 17px;
    color: var(--ink);
    line-height: 1.2;
  }
  .rule {
    height: 1px;
    background: var(--line);
    margin: 16px 0 14px;
  }
  .contact-text {
    font-size: 18px;
    line-height: 26px;
  }
  .contact-list .row {
    height: 26px;
  }
  .contact-list .row svg {
    top: 4px;
  }
  .base-strip {
    position: absolute;
    left: 0;
    right: 0;
    bottom: 0;
    height: 10px;
    background: var(--slate);
  }
  .web-band {
    position: absolute;
    left: 300px;
    bottom: 0;
    width: 350px;
    height: 58px;
    background: var(--blue);
    color: #ffffff;
    font-size: 20px;
    letter-spacing: 2px;
    line-height: 56px;
    text-align: center;
  }
</style>
</head>
<body>
<main class="canvas">

  <section class="card card-back" aria-label="Card back">
    <div class="back-wordmark">Veltra Partners</div>
    <p class="back-tagline">Guiding strategy<span class="dot"></span>building results</p>
  </section>

  <section class="card card-front" aria-label="Card front">
    <div class="front-wordmark">Veltra Partners</div>

    <div class="details">
      <div class="row">
        <svg viewBox="0 0 24 24" style="top:4px" aria-hidden="true"><circle cx="12" cy="7" r="5"/><path d="M2 23c0-6 4.5-9 10-9s10 3 10 9z"/></svg>
        <div class="person-name">DANIEL REYES</div>
        <div class="person-title">CEO/FOUNDER</div>
      </div>

      <div class="rule"></div>

      <div class="row">
        <svg viewBox="0 0 24 24" style="top:4px" aria-hidden="true"><path d="M12 1a8 8 0 0 0-8 8c0 6 8 14 8 14s8-8 8-14a8 8 0 0 0-8-8zm0 11a3 3 0 1 1 0-6 3 3 0 0 1 0 6z"/></svg>
        <div class="contact-text">412 Birchwood Court<br>Juneau, Alaska 99801</div>
      </div>

      <div class="rule"></div>

      <div class="contact-list">
        <div class="row">
          <svg viewBox="0 0 24 24" aria-hidden="true"><path d="M6.6 10.8a15 15 0 0 0 6.6 6.6l2.2-2.2a1 1 0 0 1 1-.25 11.4 11.4 0 0 0 3.6.57 1 1 0 0 1 1 1V20a1 1 0 0 1-1 1A17 17 0 0 1 3 4a1 1 0 0 1 1-1h3.5a1 1 0 0 1 1 1c0 1.25.2 2.45.57 3.6a1 1 0 0 1-.25 1z"/></svg>
          <div class="contact-text">555 214 7730</div>
        </div>
        <div class="row">
          <svg viewBox="0 0 24 24" aria-hidden="true"><path d="M7 1h10a2 2 0 0 1 2 2v18a2 2 0 0 1-2 2H7a2 2 0 0 1-2-2V3a2 2 0 0 1 2-2zm0 3v14h10V4z"/></svg>
          <div class="contact-text">555 903 4186</div>
        </div>
        <div class="row">
          <svg viewBox="0 0 24 24" aria-hidden="true"><path d="M2 5h20v14H2zm2 2v.5l8 5 8-5V7l-8 5z"/></svg>
          <div class="contact-text">daniel@veltrapartners.com</div>
        </div>
      </div>
    </div>

    <div class="base-strip"></div>
    <div class="web-band">www.veltrapartners.com</div>
  </section>

</main>
</body>
</html>
```